Bright Harbor Counseling Letterhead for hip modern business

I would like some ombre use of the colors in the logo hip letterhead that incorporates logo colors and feel, needs to connect with young professionals and college students. i need to be able to write letters to schools to excuse absences as well. i like color blocks on one side preferably using colors from the attached logo design.

Target Market(s)

high income young people, young adults and college students

Industry/Entity Type

mental health

Font styles to use
Serif
Sans Serif

Colors
0054AA
0677BA
7BADD7
CADEEF
E8F1F8
0094D4
00A9DD
6FCCEA
C7EBF8
E9F6FB
00AB8E
00BBA5
67D7C9
C6EFE9
E9F9F6
59FF00
82FF00
B8FF75
E3FFCB
F4FFEA
A7469A
B969AE
D3A5CF
EDDBEB
F8F0F9
6B429C
8869AF
B7A5CE
E3DAEB
F3F0F8

Requirements
Must have
• a modern hip feel, somewhat color

```html
<!DOCTYPE html>
<html lang="en">
<head>
<meta charset="utf-8">
<title>Bright Harbor Counseling — Letterhead</title>
<link rel="stylesheet" href="https://fonts.googleapis.com/css2?family=Mulish:wght@300;400&display=swap">
<style>
  :root {
    --backdrop: #2e2e2e;
    --paper: #ffffff;
    --ink: #3a3a3a;
    --navy-blue: #0677ba;
    --sky-blue: #0094d4;
    --teal: #00bba5;
    --violet: #6b429c;
    --plum: #a7469a;
    --indigo: #4a67b5;
  }
  html, body {
    margin: 0;
    width: 1200px;
    height: 1064px;
    overflow: hidden;
    background: var(--backdrop);
    font-family: "Mulish", Arial, sans-serif;
  }
  .letterhead {
    position: absolute;
    left: 253px;
    top: 42px;
    width: 693px;
    height: 980px;
    background: var(--paper);
    box-shadow: 0 10px 30px rgba(0,0,0,0.45);
    overflow: hidden;
  }
  .color-blocks {
    position: absolute;
    left: 0;
    top: 0;
    width: 22px;
    height: 100%;
    display: flex;
    flex-direction: column;
  }
  .color-blocks span { flex: 1; }
  .block-teal { background: var(--teal); }
  .block-sky { background: var(--sky-blue); }
  .block-navy { background: var(--navy-blue); }
  .block-indigo { background: var(--indigo); }
  .block-violet { background: var(--violet); }
  .block-plum { background: var(--plum); }
  .brand {
    position: absolute;
    left: 58px;
    top: 58px;
    display: flex;
    align-items: flex-start;
    gap: 10px;
    color: var(--ink);
  }
  .brand-dot {
    width: 20px;
    height: 20px;
    border-radius: 50%;
    background: var(--plum);
    margin-top: 5px;
  }
  .brand-name {
    margin: 0;
    font-size: 27px;
    line-height: 1;
    font-weight: 300;
    letter-spacing: 0.3px;
  }
  .brand-name span {
    display: block;
    font-size: 15px;
    letter-spacing: 3px;
    text-align: right;
    margin-top: 6px;
  }
  .contact {
    position: absolute;
    right: 40px;
    top: 52px;
    font-size: 10.5px;
    line-height: 1.5;
    color: var(--ink);
    font-style: normal;
    text-align: left;
  }
  .contact p { margin: 0; }
  .contact ul { list-style: none; margin: 3px 0 0; padding: 0; }
  .contact li { display: flex; align-items: center; gap: 6px; }
  .contact-icon {
    width: 11px;
    height: 11px;
    border-radius: 50%;
    display: inline-flex;
    align-items: center;
    justify-content: center;
  }
  .contact-icon svg { width: 7px; height: 7px; }
  .icon-phone { background: var(--teal); }
  .icon-fax { background: var(--plum); }
  .icon-mail { background: var(--navy-blue); }
  .header-rule {
    position: absolute;
    left: 58px;
    right: 40px;
    top: 138px;
    height: 1px;
    background: linear-gradient(90deg, var(--teal), var(--navy-blue), var(--plum));
    opacity: 0.6;
  }
  .footer-band {
    position: absolute;
    left: 22px;
    right: 0;
    bottom: 0;
    height: 44px;
    background: linear-gradient(90deg, var(--teal) 0%, var(--navy-blue) 40%, var(--indigo) 70%, var(--violet) 100%);
    display: flex;
    align-items: center;
    justify-content: flex-end;
    padding-right: 40px;
    box-sizing: border-box;
  }
  .footer-web {
    color: #ffffff;
    font-size: 12px;
    letter-spacing: 0.6px;
    font-weight: 400;
  }
</style>
</head>
<body>
  <main class="letterhead">
    <div class="color-blocks" aria-hidden="true">
      <span class="block-teal"></span>
      <span class="block-sky"></span>
      <span class="block-navy"></span>
      <span class="block-indigo"></span>
      <span class="block-violet"></span>
      <span class="block-plum"></span>
    </div>

    <header class="brand">
      <h1 class="brand-name">Bright Harbor<span>Counseling</span></h1>
      <div class="brand-dot"></div>
    </header>

    <address class="contact">
      <p>Suite 210 Harbor Lane,</p>
      <p>Portland, OR 97205, USA</p>
      <ul>
        <li><span class="contact-icon icon-phone"><svg viewBox="0 0 10 10"><path fill="#fff" d="M2 1 L4 1 L4.6 3 L3.5 4 C4 5.2 4.8 6 6 6.5 L7 5.4 L9 6 L9 8 C9 8.6 8.6 9 8 9 C4.2 8.8 1.2 5.8 1 2 C1 1.4 1.4 1 2 1 Z"/></svg></span>(503) 555 0142</li>
        <li><span class="contact-icon icon-fax"><svg viewBox="0 0 10 10"><rect x="2" y="1.5" width="6" height="7" fill="#fff"/></svg></span>(503) 555 0143</li>
        <li><span class="contact-icon icon-mail"><svg viewBox="0 0 10 10"><rect x="1" y="2.5" width="8" height="5" fill="#fff"/><path d="M1 2.5 L5 5.5 L9 2.5" fill="none" stroke="#0677ba" stroke-width="0.8"/></svg></span>hello@brightharborcounseling.com</li>
      </ul>
    </address>

    <div class="header-rule" aria-hidden="true"></div>

    <footer class="footer-band">
      <span class="footer-web">www.brightharborcounseling.com</span>
    </footer>
  </main>
</body>
</html>
```